Commercial Loan Originator Business Card (CHANGE COLORS SCHEME)

CHANGE COLOR SCHEME - SAME DESIGN

Name Marlene Agate
Title Commercial Loan Originator
Office (800) 417-2906 x68
Direct (240) 615-2043
Email freshgreens4life@quillbox.example

Name Dale Morrow
Office (800) 417-2906 x70
Direct (410) 392-5184
Email d.morthehomeguy@quillbox.example

Name Leonard Vasko
Office (800) 417-2906 x71
Direct (215) 463-0712
Email l.vasko41@quillbox.example

Name Gwen Halsey
Office (800) 417-2906 x
Direct (202) 548-1370
Email ghalsey63@quillbox.example

Name Mirna Ashby
Office (800) 417-2906 x72
Direct (240) 871-4526
Email tristatehomelending@quillbox.example

```html
<!DOCTYPE html>
<html lang="en">
<head>
<meta charset="utf-8">
<title>Dale Morrow – Commercial Loan Originator</title>
<link rel="stylesheet" href="https://fonts.googleapis.com/css2?family=Montserrat:wght@400;700&display=swap">
<style>
  :root {
    --backdrop: #d9dadc;
    --card: #ffffff;
    --accent: #0e6b62;
    --ink: #263330;
    --jacket: #4a5648;
    --jacket-dark: #2b322c;
  }
  * { margin: 0; padding: 0; box-sizing: border-box; }
  html, body { width: 1200px; height: 788px; overflow: hidden; }
  body {
    background: var(--backdrop);
    font-family: "Montserrat", Arial, sans-serif;
    position: relative;
  }
  .business-card {
    position: absolute;
    left: 100px; top: 108px;
    width: 1000px; height: 572px;
    background: var(--card);
    border-radius: 22px;
    border-bottom: 5px solid var(--accent);
    border-left: 2px solid var(--accent);
    border-right: 2px solid var(--accent);
    overflow: hidden;
    box-shadow: 0 10px 28px rgba(0,0,0,.18);
  }
  .portrait {
    position: absolute;
    left: 20px; bottom: 0;
    width: 410px; height: 470px;
    border-radius: 170px 170px 0 0;
    background: linear-gradient(180deg, #6f6a66 0%, var(--jacket) 35%, var(--jacket-dark) 100%);
  }
  .contact-block {
    position: absolute;
    right: 40px; top: 150px;
    width: 500px;
    text-align: right;
  }
  .name {
    color: var(--accent);
    font-weight: 700;
    font-size: 40px;
    letter-spacing: 1px;
    line-height: 1;
    text-transform: uppercase;
    margin-right: 34px;
  }
  .title {
    color: var(--ink);
    font-size: 22px;
    margin-top: 6px;
    margin-right: 34px;
  }
  .divider {
    width: 18px; height: 2px;
    background: var(--accent);
    margin: 14px 34px 16px auto;
  }
  .contact-line {
    display: flex;
    justify-content: flex-end;
    align-items: center;
    gap: 14px;
    color: var(--ink);
    font-size: 22px;
    line-height: 1.9;
    white-space: nowrap;
  }
  .contact-line svg { width: 20px; height: 20px; flex: none; }
</style>
</head>
<body>
  <div class="business-card">
    <div class="portrait" role="img" aria-label="Portrait photo of Dale Morrow in a green plaid blazer, hands on hips"></div>
    <div class="contact-block">
      <h1 class="name">Dale Morrow</h1>
      <p class="title">Commercial Loan Originator</p>
      <div class="divider"></div>
      <p class="contact-line">(800) 417-2906 x70
        <svg viewBox="0 0 24 24" aria-hidden="true"><path fill="#0e6b62" d="M6.6 10.8a15 15 0 0 0 6.6 6.6l2.2-2.2a1 1 0 0 1 1-.25 11 11 0 0 0 3.6.6 1 1 0 0 1 1 1V20a1 1 0 0 1-1 1A17 17 0 0 1 3 4a1 1 0 0 1 1-1h3.5a1 1 0 0 1 1 1c0 1.25.2 2.45.6 3.6a1 1 0 0 1-.25 1z"/></svg>
      </p>
      <p class="contact-line">(410) 392-5184
        <svg viewBox="0 0 24 24" aria-hidden="true"><rect x="6" y="2" width="12" height="20" rx="2" fill="none" stroke="#0e6b62" stroke-width="2.2"/><circle cx="12" cy="18" r="1.2" fill="#0e6b62"/></svg>
      </p>
      <p class="contact-line">d.morthehomeguy@quillbox.example
        <svg viewBox="0 0 24 24" aria-hidden="true"><rect x="2" y="5" width="20" height="14" rx="1" fill="#0e6b62"/><path d="M2.5 5.5 12 13l9.5-7.5" fill="none" stroke="#fff" stroke-width="1.6"/></svg>
      </p>
    </div>
  </div>
</body>
</html>
```